Modern Business Card for Larkwell 2018

Our company assumes the best about people. We are creating an online community of entrepreneurs and business leaders who struggle with marketing their business online.

This business card should POP! We recently got a new logo and are launching a new website next month, so our business cards should make a statement that feels:
-Fresh
-Smart
-Trustworthy
-Fun

Target Market(s)

small business owners, entrepreneurs

Industry/Entity Type

Digital Marketing

Contact Information for Business Card

Dimensions: 3.5" x 2"

Font styles to use
Sans Serif

Colors
f37122
ffffff

Requirements
Must have
• We need a business card with a modern, bold design. We will use one side of the card as a lead-generation offer, so text on one side will need to fit up to 140 characters. The business card should stick to our core colors (orange, black, and white).
Nice to have
• We think a vertical "portrait" design could be interesting.
Should not have
• Should not look like a traditional business card. The round icon should stand out from a distance.

```html
<!DOCTYPE html>
<html lang="en">
<head>
<meta charset="UTF-8">
<title>Larkwell Business Card</title>
<link rel="stylesheet" href="https://fonts.googleapis.com/css2?family=Roboto:wght@400;500;700;900&family=Lobster&display=swap">
<style>
  :root {
    --brand-orange: #f26724;
    --ink-black: #000000;
    --paper-white: #f4f4f4;
    --pure-white: #ffffff;
    --backdrop: #e7e3de;
    --rule-grey: #3a3a3a;
  }
  * { margin: 0; padding: 0; box-sizing: border-box; }
  html, body {
    width: 1200px;
    height: 960px;
    overflow: hidden;
  }
  body {
    position: relative;
    background: var(--backdrop);
    font-family: "Roboto", Arial, sans-serif;
  }
  .card {
    position: absolute;
    width: 600px;
    height: 342px;
    border-radius: 20px;
    background: var(--paper-white);
    overflow: hidden;
  }
  /* Front */
  .card--front { left: 314px; top: 113px; }
  .brand-mark {
    position: absolute;
    left: 48px;
    top: 29px;
    display: flex;
    align-items: center;
    gap: 16px;
  }
  .brand-mark__dot {
    width: 124px;
    height: 124px;
    border-radius: 50%;
    background: var(--brand-orange);
  }
  .brand-mark__name {
    font-weight: 700;
    font-size: 32px;
    color: var(--brand-orange);
  }
  .identity-band {
    position: absolute;
    left: 257px;
    top: 162px;
    width: 343px;
    height: 147px;
    background: var(--ink-black);
    color: var(--pure-white);
    padding: 20px 0 0 69px;
  }
  .identity-band__role {
    font-size: 18px;
    letter-spacing: 0.4px;
    white-space: nowrap;
  }
  .identity-band__name {
    font-family: "Lobster", cursive;
    font-size: 31px;
    line-height: 1.15;
    margin-top: 8px;
    margin-left: -8px;
    letter-spacing: -0.5px;
    white-space: nowrap;
  }
  .identity-band__email {
    font-size: 15px;
    letter-spacing: 2.6px;
    margin-top: 8px;
    white-space: nowrap;
  }
  /* Back */
  .card--back { left: 311px; top: 472px; }
  .offer-panel {
    position: absolute;
    left: 0; top: 0;
    width: 600px;
    height: 218px;
    background: var(--brand-orange);
    color: var(--pure-white);
  }
  .offer-panel__brand {
    position: absolute;
    left: 40px;
    top: 58px;
    width: 240px;
    text-align: center;
  }
  .offer-panel__dot {
    width: 36px;
    height: 36px;
    border-radius: 50%;
    background: var(--pure-white);
    margin: 0 auto 12px;
  }
  .offer-panel__name {
    font-weight: 900;
    font-size: 37px;
    letter-spacing: 3px;
    line-height: 1;
  }
  .offer-panel__tagline {
    font-size: 12px;
    font-weight: 500;
    letter-spacing: 0.6px;
    margin-top: 8px;
    white-space: nowrap;
  }
  .offer-panel__divider {
    position: absolute;
    left: 297px;
    top: 25px;
    width: 1px;
    height: 168px;
    background: rgba(255,255,255,0.7);
  }
  .offer-panel__copy {
    position: absolute;
    left: 322px;
    top: 30px;
  }
  .offer-panel__headline {
    font-weight: 700;
    font-size: 20px;
    line-height: 21.5px;
    white-space: nowrap;
  }
  .offer-panel__body {
    font-size: 15.5px;
    line-height: 20px;
    margin-top: 5px;
    white-space: nowrap;
  }
  .offer-panel__url {
    font-weight: 700;
    font-size: 20px;
    margin-top: 5px;
    white-space: nowrap;
  }
  .notes-line {
    position: absolute;
    left: 36px;
    width: 520px;
    height: 1px;
    background: var(--rule-grey);
  }
  .notes-line--first { top: 260px; }
  .notes-line--second { top: 300px; }
</style>
</head>
<body>
  <section class="card card--front">
    <div class="brand-mark">
      <div class="brand-mark__dot"></div>
      <span class="brand-mark__name">Larkwell</span>
    </div>
    <div class="identity-band">
      <p class="identity-band__role">STORY MARKETING COACH</p>
      <p class="identity-band__name">DANA WHITFIELD</p>
      <p class="identity-band__email">dana@larkwellhq.com</p>
    </div>
  </section>

  <section class="card card--back">
    <div class="offer-panel">
      <div class="offer-panel__brand">
        <div class="offer-panel__dot"></div>
        <p class="offer-panel__name">LARKWELL</p>
        <p class="offer-panel__tagline">TELL STORIES THAT INSPIRE ACTION</p>
      </div>
      <div class="offer-panel__divider"></div>
      <div class="offer-panel__copy">
        <p class="offer-panel__headline">REACH MORE PEOPLE.<br>MAKE MORE MONEY.<br>CREATE MORE IMPACT.</p>
        <p class="offer-panel__body">Get your free Larkwell<br>Starter Package and our<br>marketing guide today at</p>
        <p class="offer-panel__url">Larkwellhq.com/start</p>
      </div>
    </div>
    <div class="notes-line notes-line--first"></div>
    <div class="notes-line notes-line--second"></div>
  </section>
</body>
</html>
```